New website for salon services and wedding hair and makeup

I am a professional hairstylist and makeup artist in Charleston, SC. I have my own company where I see clients for cut and color and I also go on site for weddings. I have a current website that I would like to update and change the style. I would like to add a contact form, map, additional pages and be mobile friendly. It is important to me that it have a site map and can show up in searches. I will need to add photos to the site every so often and would like to continue to work with the designer. I have a logo that I am happy with and have attached the file however if you think a new logo would help the look of the site I am open to it. My current website is www.brightcombstudio-example.com, I would like to change the style and layout so it looks up to date. Here are some links to sites that I like the look of but I don't want to limit your creativity. http://willowlanefolio-example.com/ http://www.runwaylensworks-example.com http://miraventhol-example.com/. I have attached a few files for mock up purposes, please let me know if you would like more content. Thank you!

Target Market(s)

Women, Brides

Industry/Entity Type

Hair And Beauty

Number of Pages Required

1 page

Font styles to use
Sans Serif
Script

Requirements
Must have
• Contact form, Mobile friendly, sitemap
Nice to have
• I really like the look for the sites I have included on the project description guide.
Should not have
• Nothing overly girly.

```html
<!DOCTYPE html>
<html lang="en">
<head>
<meta charset="utf-8">
<title>Brightcomb Studio – Hair and Makeup</title>
<link href="https://fonts.googleapis.com/css2?family=Oswald:wght@400;500;600&family=Great+Vibes&family=Open+Sans:wght@400;600&display=swap" rel="stylesheet">
<style>
:root{
  --navy:#0d3557;
  --navy-deep:#0a2a46;
  --nav-active:#3d6a8c;
  --teal:#3fb3b8;
  --ink:#1e3550;
  --body:#3b4656;
  --gallery:#3b3b3d;
  --white:#ffffff;
}
*{margin:0;padding:0;box-sizing:border-box}
html,body{width:1200px;height:3512px;overflow:hidden}
body{font-family:"Open Sans",sans-serif;color:var(--body);background:var(--white);position:relative}
.block{position:absolute;left:0;width:1200px}

/* hero */
.hero{top:0;height:792px;background:linear-gradient(180deg,#f3f4f6,#dfe2e6);overflow:hidden}
.hero-bride{position:absolute;left:560px;top:0;width:460px;height:792px;background:radial-gradient(ellipse at 50% 45%,#e8dccb 0%,#cdbda7 45%,rgba(215,210,205,0) 75%)}
.hero-ribbon{position:absolute;left:0;top:670px;width:1200px;height:90px;background:linear-gradient(90deg,rgba(125,45,140,.85),rgba(150,70,165,.55) 50%,rgba(125,45,140,.85))}
.hero-flowers{position:absolute;left:1010px;top:230px;width:190px;height:330px;background:linear-gradient(180deg,rgba(160,120,200,.45),rgba(120,150,110,.35))}
.logo{position:absolute;left:90px;top:60px;height:110px;display:flex;align-items:center;gap:16px;white-space:nowrap}
.logo-dot{width:46px;height:46px;border-radius:50%;background:var(--teal)}
.logo-name{font-family:"Open Sans",sans-serif;font-weight:600;font-size:38px;color:var(--navy)}
.hero-title{position:absolute;left:100px;top:320px;font-family:"Oswald",sans-serif;font-weight:500;font-size:80px;line-height:100px;color:var(--navy);letter-spacing:3px;text-transform:uppercase;white-space:nowrap}

/* nav */
.nav{top:792px;height:80px;background:var(--navy);display:flex;padding-left:120px}
.nav a{display:block;width:180px;height:80px;line-height:80px;text-align:center;color:var(--white);font-size:22px;text-decoration:none;text-transform:uppercase;letter-spacing:1px}
.nav a.active{background:var(--nav-active)}

/* welcome */
.welcome{top:872px;height:680px;background:linear-gradient(100deg,#d7e6e7 0%,#b7d4d3 40%,#cfe3e2 100%)}
.welcome-photo{position:absolute;left:140px;top:88px;width:400px;height:488px;background:linear-gradient(180deg,#e7a974 0%,#8c7898 40%,#3e4250 100%)}
.welcome-text{position:absolute;left:600px;top:70px;width:560px}
.script-title{font-family:"Great Vibes",cursive;font-size:58px;color:var(--ink);line-height:60px}
.welcome h2{font-family:"Oswald",sans-serif;font-weight:500;font-size:58px;letter-spacing:3px;color:var(--ink);text-transform:uppercase;line-height:70px;margin-bottom:22px}
.welcome p{font-size:17px;line-height:27px;margin-bottom:20px;color:var(--body)}

/* gallery */
.gallery{top:1552px;height:348px;background:var(--gallery)}
.section-title{font-family:"Oswald",sans-serif;font-weight:500;text-transform:uppercase;letter-spacing:2px}
.gallery .section-title{position:absolute;left:80px;top:22px;font-size:70px;color:var(--white)}
.thumb{position:absolute;top:128px;width:230px;height:160px}
.arrow{position:absolute;top:190px}

/* services */
.services{top:1900px;height:720px;background:linear-gradient(180deg,#fbe6ee 0%,#f6bfd3 45%,#fbe1ea 100%)}
.services .section-title{position:absolute;left:80px;top:30px;font-size:70px;color:var(--ink)}
.service{position:absolute;top:140px;width:240px;text-align:center}
.service-photo{width:200px;height:200px;border-radius:50%;margin:0 auto;border:6px solid var(--navy)}
.service h3{font-family:"Open Sans",sans-serif;font-weight:400;font-size:24px;color:var(--ink);margin:16px 0 10px}
.service p{font-size:15px;line-height:23px;color:var(--body)}
.extensions{position:absolute;left:0;width:1200px;top:620px;text-align:center;font-weight:600;font-size:22px;color:var(--ink)}

/* contact */
.contact{top:2620px;height:500px;background:var(--white)}
.contact .section-title{position:absolute;left:80px;top:30px;font-size:70px;color:var(--ink)}
.contact-info{position:absolute;left:80px;top:150px;width:420px;font-size:16px;line-height:26px}
.contact-info .line{display:flex;align-items:center;gap:12px;margin-top:14px}
.social{display:flex;gap:16px;margin-top:26px}
.social span{width:38px;height:38px;background:var(--navy);display:block}
.contact-photo{position:absolute;left:560px;top:0;width:640px;height:500px;background:linear-gradient(160deg,#e9d8c8 0%,#c9ad95 50%,#8d7f7a 100%)}
.form{position:absolute;left:600px;top:90px;width:560px}
.form .row{display:flex;gap:20px;margin-bottom:22px}
.field{flex:1;height:44px;background:rgba(255,255,255,.88);font-size:16px;color:#6b7280;padding:11px 12px}
.field.msg{height:140px}
.submit{width:140px;height:46px;background:var(--navy);color:var(--white);font-size:18px;text-align:center;line-height:46px;letter-spacing:1px}

/* map */
.map{top:3120px;height:272px;background:linear-gradient(120deg,#a9c9e3 0%,#d9e3c8 50%,#a9c9e3 100%)}

/* footer */
.footer{top:3392px;height:120px;background:var(--navy-deep);text-align:center;color:var(--white)}
.footer nav{padding-top:26px;font-size:17px}
.footer nav a{color:var(--white);text-decoration:none;margin:0 28px;text-transform:uppercase}
.footer small{display:block;margin-top:22px;font-size:15px}
</style>
</head>
<body>

<header class="block hero">
  <div class="hero-bride" role="img" aria-label="Photo of a bride in a lace wedding gown holding a bouquet"></div>
  <div class="hero-flowers" role="img" aria-label="Photo of lavender flowers"></div>
  <div class="hero-ribbon" role="img" aria-label="Photo of a purple satin ribbon"></div>
  <div class="logo">
    <span class="logo-dot"></span>
    <span class="logo-name">Brightcomb Studio</span>
  </div>
  <h1 class="hero-title">Chic<br>Sophisticated<br>Inspired</h1>
</header>

<nav class="block nav">
  <a class="active" href="#about">About</a>
  <a href="#gallery">Gallery</a>
  <a href="#services">Services</a>
  <a href="#contact">Contact</a>
</nav>

<section class="block welcome" id="about">
  <div class="welcome-photo" role="img" aria-label="Photo of a bride and groom embracing on a pier at sunset"></div>
  <div class="welcome-text">
    <div class="script-title">Welcome</div>
    <h2>Brightcomb</h2>
    <p>Brightcomb Studio specializes in providing gorgeous, long lasting hair and makeup. With over nine years of experience and training, we know how to make your day the very best. We take pride in client satisfaction and helping you achieve the look of your dreams while making the experience memorable and enjoyable. We work on location so you can relax and finish your day with the people you love.</p>
    <p>If your needs are of a more professional nature we have you covered. Our team has years of experience in editorial and fashion work, giving you camera ready results for every shoot and event.</p>
    <p>We also provide services in studio and are happy to meet all of your hair care needs.</p>
  </div>
</section>

<section class="block gallery" id="gallery">
  <h2 class="section-title">Gallery</h2>
  <svg class="arrow" style="left:30px" width="24" height="40" viewBox="0 0 24 40"><path d="M20 4 L4 20 L20 36" fill="none" stroke="#ffffff" stroke-width="4"/></svg>
  <div class="thumb" style="left:80px;background:linear-gradient(135deg,#f1ebe3,#b9a48c)" role="img" aria-label="Photo of a bride and groom"></div>
  <div class="thumb" style="left:345px;background:linear-gradient(135deg,#6d8fb0,#d7b895)" role="img" aria-label="Photo of a woman with styled hair"></div>
  <div class="thumb" style="left:610px;background:linear-gradient(135deg,#d9d9d9,#4d4d4d)" role="img" aria-label="Black and white photo of a wedding party"></div>
  <div class="thumb" style="left:875px;background:linear-gradient(135deg,#9cc4de,#e5d2bc)" role="img" aria-label="Photo of a couple on the beach"></div>
  <svg class="arrow" style="left:1146px" width="24" height="40" viewBox="0 0 24 40"><path d="M4 4 L20 20 L4 36" fill="none" stroke="#ffffff" stroke-width="4"/></svg>
</section>

<section class="block services" id="services">
  <h2 class="section-title">Our Services</h2>
  <div class="service" style="left:40px">
    <div class="service-photo" style="background:linear-gradient(135deg,#f0e6dc,#a88f78)" role="img" aria-label="Photo of a bride"></div>
    <h3>Bridal</h3>
    <p>Thank you for your interest in our on location bridal services. Please contact us for more information.</p>
  </div>
  <div class="service" style="left:320px">
    <div class="service-photo" style="background:linear-gradient(135deg,#e8c27a,#8a5a34)" role="img" aria-label="Photo of a woman with a fresh haircut"></div>
    <h3>Hair Cut</h3>
    <p>Women $50<br>Men $30</p>
  </div>
  <div class="service" style="left:600px">
    <div class="service-photo" style="background:linear-gradient(135deg,#f3d8c4,#c06a3e)" role="img" aria-label="Photo of a woman with coloured hair"></div>
    <h3>Color</h3>
    <p>Partial Highlights $130+<br>Full Highlights $160+<br>Double Process $150+<br>Ombre $125+<br>Roots with Glaze $110+<br>All Over Color $85+<br>All color services include a complimentary hair cut and blowout</p>
  </div>
  <div class="service" style="left:880px">
    <div class="service-photo" style="background:linear-gradient(135deg,#d8c3b2,#6b4a3a)" role="img" aria-label="Photo of a woman with a styled updo"></div>
    <h3>Styling &amp; Treatments</h3>
    <p>Blow out/Heat Styling $30<br>Event Updo $85<br>Deep Condition $15<br>Keratin Smoothing Treatment $150+</p>
  </div>
  <div class="extensions">Hair Extensions – Complimentary Consultation</div>
</section>

<section class="block contact" id="contact">
  <h2 class="section-title">Contact Us</h2>
  <div class="contact-info">
    <p>Have a question, desire more information, or just want to have a chat?</p>
    <p style="margin-top:14px">Please contact us:</p>
    <div class="line">
      <svg width="20" height="20" viewBox="0 0 24 24"><path d="M6.6 10.8a15 15 0 0 0 6.6 6.6l2.2-2.2a1 1 0 0 1 1-.25 11 11 0 0 0 3.6.6 1 1 0 0 1 1 1V20a1 1 0 0 1-1 1A17 17 0 0 1 3 4a1 1 0 0 1 1-1h3.5a1 1 0 0 1 1 1 11 11 0 0 0 .6 3.6 1 1 0 0 1-.25 1z" fill="#0d3557"/></svg>
      <span>843-555-0142</span>
    </div>
    <div class="line">
      <svg width="20" height="20" viewBox="0 0 24 24"><rect x="2" y="5" width="20" height="14" fill="none" stroke="#0d3557" stroke-width="2"/><path d="M2 5 L12 13 L22 5" fill="none" stroke="#0d3557" stroke-width="2"/></svg>
      <span>hello@brightcombstudio-example.com</span>
    </div>
    <p style="margin-top:14px">We look forward to hearing from you!</p>
    <div class="social"><span></span><span></span><span></span></div>
  </div>
  <div class="contact-photo" role="img" aria-label="Photo of a bride's hair being styled with flowers"></div>
  <div class="form">
    <div class="row"><div class="field">Enter Name</div><div class="field">Enter Email</div></div>
    <div class="row"><div class="field">Enter Contact No.</div><div class="field">Enter Subject</div></div>
    <div class="row"><div class="field msg">Message</div></div>
    <div class="submit">SUBMIT</div>
  </div>
</section>

<div class="block map" role="img" aria-label="Map of the Charleston coastline"></div>

<footer class="block footer">
  <nav>
    <a href="#">Home</a><a href="#about">About</a><a href="#gallery">Gallery</a><a href="#services">Services</a><a href="#contact">Contact</a>
  </nav>
  <small>© Brightcomb Studio, 2015. All Rights Reserved.</small>
</footer>

</body>
</html>
```